Stationery Design Project

I need a stationary design for our company. we are based in Houston, TX and we are called Mira Vell Lending. And we are wanting to brand our MoneyMendPlus program, which includes our tax preparation and restoration, credit repair service. Although our business offers other programs, we are interested in mainly focusing on The MoneyMendPlus program. We are looking for way to brand our ourselves and I believe that a great stationery design will help in achieving this goal. Our logo design is blue and light blue. the slogan is orange.

Industry/Entity Type

Business

Requirements
Must have
• Address: 30871 Calloway Ln. B-22
Houston, TX 75419
Tel. 555-318-6207
Fax 555-294-7153
www.miravelllending.example
info@miravelllending.example
Our Slogan: Confidence, Renewed!

```html
<!DOCTYPE html>
<html lang="en">
<head>
<meta charset="utf-8">
<title>MoneyMendPlus Business Card</title>
<link href="https://fonts.googleapis.com/css2?family=Tinos:wght@400;700&family=Roboto+Slab:wght@700&display=swap" rel="stylesheet">
<style>
  :root {
    --backdrop: #ece7e1;
    --card-white: #ffffff;
    --navy: #153f68;
    --brand-blue: #1f6fa8;
    --sky: #2b9ad6;
    --orange: #f39a1e;
    --ink: #2b2b2b;
    --divider: #c9c9c9;
  }
  * { margin: 0; padding: 0; box-sizing: border-box; }
  html, body { width: 1200px; height: 390px; overflow: hidden; }
  body { background: var(--backdrop); position: relative; font-family: "Tinos", "Times New Roman", serif; }

  .card {
    position: absolute;
    top: 40px;
    width: 560px;
    height: 318px;
    border-radius: 24px;
    overflow: hidden;
  }
  .card-front { left: 27px; background: var(--card-white); }
  .card-back { left: 615px; background: var(--navy); }

  .brand {
    position: absolute;
    left: 0;
    width: 340px;
    top: 132px;
    text-align: center;
  }
  .brand-name {
    font-family: "Tinos", "Times New Roman", serif;
    font-size: 38px;
    color: var(--brand-blue);
    line-height: 1;
  }
  .brand-slogan {
    margin-top: 16px;
    font-family: "Roboto Slab", serif;
    font-weight: 700;
    font-size: 18px;
    letter-spacing: 1.6px;
    color: var(--orange);
  }

  .divider {
    position: absolute;
    left: 315px;
    top: 57px;
    width: 1px;
    height: 152px;
    background: var(--divider);
  }

  .contact {
    position: absolute;
    left: 335px;
    top: 66px;
    color: var(--ink);
    font-size: 15px;
    line-height: 19px;
  }
  .contact-address { margin-bottom: 14px; }
  .contact-list { list-style: none; }
  .contact-list li { display: flex; align-items: center; height: 22.5px; font-size: 14.5px; }
  .contact-list svg { width: 12px; height: 12px; margin-right: 6px; fill: var(--ink); flex: none; }

  .waves { position: absolute; left: 0; bottom: 0; width: 560px; height: 90px; }

  .back-name {
    position: absolute;
    left: 0; right: 0;
    top: 118px;
    text-align: center;
    color: #ffffff;
    font-size: 32px;
    letter-spacing: 1px;
  }
  .back-url {
    position: absolute;
    left: 0; right: 0;
    top: 272px;
    text-align: center;
    color: #ffffff;
    font-size: 14px;
    letter-spacing: 2.6px;
  }
  .back-url b { font-weight: 700; }
</style>
</head>
<body>

<section class="card card-front">
  <div class="brand">
    <div class="brand-name">MoneyMendPlus</div>
    <div class="brand-slogan">Confidence, Renewed!</div>
  </div>

  <div class="divider"></div>

  <div class="contact">
    <p class="contact-address">30871 Calloway Ln. B-22<br>Houston, TX 75419</p>
    <ul class="contact-list">
      <li><svg viewBox="0 0 12 12"><circle cx="6" cy="6" r="5.5" fill="none" stroke="#2b2b2b"/><path d="M3.6 3.2l1.3-.4.8 1.6-.8.6c.3.8.9 1.4 1.7 1.7l.6-.8 1.6.8-.4 1.3C6 8.2 3.6 5.8 3.6 3.2z"/></svg>555-318-6207</li>
      <li><svg viewBox="0 0 12 12"><rect x="3" y="1" width="6" height="3"/><rect x="0.5" y="4.5" width="11" height="5" rx="1"/><rect x="3" y="8" width="6" height="3" fill="#fff" stroke="#2b2b2b" stroke-width="0.8"/></svg>555-294-7153</li>
      <li><svg viewBox="0 0 12 12"><rect x="0.5" y="2.5" width="11" height="8" rx="1"/><path d="M1 3.2l5 3.6 5-3.6" fill="none" stroke="#fff" stroke-width="1"/></svg>info@miravelllending.example</li>
      <li><svg viewBox="0 0 12 12"><circle cx="6" cy="6" r="5.5"/><path d="M0.5 6h11M6 0.5v11M2 3h8M2 9h8" stroke="#fff" stroke-width="0.7" fill="none"/><ellipse cx="6" cy="6" rx="2.4" ry="5.5" fill="none" stroke="#fff" stroke-width="0.7"/></svg>www.miravelllending.example</li>
    </ul>
  </div>

  <svg class="waves" viewBox="0 0 560 90" preserveAspectRatio="none" aria-hidden="true">
    <defs>
      <linearGradient id="wave-blue" x1="0" x2="1" y1="0" y2="0">
        <stop offset="0" stop-color="#2b9ad6"/>
        <stop offset="1" stop-color="#153f68"/>
      </linearGradient>
      <linearGradient id="wave-orange" x1="0" x2="1" y1="0" y2="0">
        <stop offset="0" stop-color="#f7b24a"/>
        <stop offset="1" stop-color="#f08a12"/>
      </linearGradient>
    </defs>
    <path d="M0 38 C120 10 240 30 330 30 C430 30 500 20 560 34 L560 90 L0 90 Z" fill="url(#wave-orange)"/>
    <path d="M0 50 C120 28 240 40 330 46 C430 52 500 38 560 42 L560 90 L0 90 Z" fill="#ffffff"/>
    <path d="M0 58 C120 36 230 52 330 58 C430 64 500 50 560 48 L560 90 L0 90 Z" fill="url(#wave-blue)"/>
  </svg>
</section>

<section class="card card-back">
  <div class="back-name">Mira Vell Lending</div>
  <div class="back-url">www.<b>miravelllending</b>.example</div>
</section>

</body>
</html>
```